Redesign of business card for Cedar Ridge Mechanical

We are looking for a new design for our business cards for Cedar Ridge Mechanical. We are a plumbing & HVAC construction company, operating on the West Coast of Canada and USA. Logo attached.
Industry/Entity Type
Construction - Plumbing & HVAC
Contact Information for Business Card
Name, address, phone numbers, email, website address
Look and feel
Each slider illustrates characteristics of the customer's brand and the style your logo design should communicate.

```html
<!DOCTYPE html>
<html lang="en">
<head>
<meta charset="UTF-8">
<title>Cedar Ridge Mechanical – Business Card</title>
<link rel="stylesheet" href="https://fonts.googleapis.com/css2?family=Oswald:wght@500;700&family=Lato:wght@400&display=swap">
<style>
  :root {
    --backdrop: #3b4045;
    --card-dark: #1c1a1a;
    --card-light: #ffffff;
    --ink: #1c1a1a;
    --ink-soft: #2b2b2b;
    --on-dark: #ffffff;
  }
  * { margin: 0; padding: 0; box-sizing: border-box; }
  html, body { width: 1200px; height: 895px; overflow: hidden; }
  body {
    background: var(--backdrop);
    position: relative;
    font-family: "Lato", sans-serif;
  }
  .card {
    position: absolute;
    left: 320px;
    width: 560px;
    height: 320px;
    border-radius: 18px;
    overflow: hidden;
  }
  .card--back { top: 60px; background: var(--card-dark); }
  .card--front { top: 500px; background: var(--card-light); color: var(--ink); }

  .brand {
    display: flex;
    align-items: center;
    gap: 14px;
    font-family: "Oswald", sans-serif;
    font-weight: 700;
    text-transform: uppercase;
    letter-spacing: 1px;
  }
  .brand__mark { display: block; border: 5px solid currentColor; }

  .card--back .brand {
    position: absolute;
    inset: 0;
    justify-content: center;
    color: var(--on-dark);
    font-size: 34px;
  }
  .card--back .brand__mark { width: 40px; height: 40px; }

  .card--front .brand {
    position: absolute;
    left: 36px;
    top: 34px;
    font-size: 20px;
    color: var(--ink);
  }
  .card--front .brand__mark { width: 26px; height: 26px; border-width: 4px; }

  .person { position: absolute; left: 36px; top: 128px; }
  .person__name {
    font-family: "Oswald", sans-serif;
    font-weight: 700;
    font-size: 26px;
    letter-spacing: 0.5px;
    text-transform: uppercase;
    line-height: 1.1;
  }
  .person__role { font-size: 17px; color: var(--ink-soft); }

  .contact { position: absolute; left: 36px; top: 212px; list-style: none; }
  .contact__item {
    display: flex;
    align-items: center;
    gap: 12px;
    font-size: 16px;
    line-height: 27px;
    color: var(--ink-soft);
  }
  .contact__icon { width: 15px; height: 15px; fill: var(--ink); flex: none; }

  .address {
    position: absolute;
    right: 34px;
    bottom: 96px;
    text-align: right;
    font-size: 16px;
    line-height: 22px;
    color: var(--ink-soft);
    font-style: normal;
  }
</style>
</head>
<body>
  <section class="card card--back" aria-label="Card back">
    <div class="brand"><span class="brand__mark"></span>Cedar Ridge Mechanical</div>
  </section>

  <section class="card card--front" aria-label="Card front">
    <div class="brand"><span class="brand__mark"></span>Cedar Ridge Mechanical</div>

    <div class="person">
      <p class="person__name">Daniel Harper</p>
      <p class="person__role">Founder and CEO</p>
    </div>

    <ul class="contact">
      <li class="contact__item">
        <svg class="contact__icon" viewBox="0 0 16 16" aria-hidden="true"><path d="M3.6 1.2l2.3 2.6-1.3 1.9c.8 1.9 2.2 3.3 4.1 4.1l1.9-1.3 2.6 2.3-1.4 2.5C6.6 13.4 2.6 9.4 1.1 4.2z"/></svg>
        604-555-0142
      </li>
      <li class="contact__item">
        <svg class="contact__icon" viewBox="0 0 16 16" aria-hidden="true"><path d="M1 3h14v1.2L8 9 1 4.2zM1 6l7 4.8L15 6v7H1z"/></svg>
        harper@cedarridgemech.com
      </li>
      <li class="contact__item">
        <svg class="contact__icon" viewBox="0 0 16 16" aria-hidden="true"><path d="M8 1a7 7 0 1 0 0 14A7 7 0 0 0 8 1zm0 1.3c.7.6 1.3 1.9 1.6 3.4H6.4C6.7 4.2 7.3 2.9 8 2.3zM2.4 7h2.7v2H2.4a5.7 5.7 0 0 1 0-2zm4 0h3.2v2H6.4zm4.5 0h2.7a5.7 5.7 0 0 1 0 2h-2.7zM6.4 10.3h3.2c-.3 1.5-.9 2.8-1.6 3.4-.7-.6-1.3-1.9-1.6-3.4z"/></svg>
        www.cedarridgemech.com
      </li>
    </ul>

    <address class="address">
      1450 Granite Avenue<br>
      Suite 200, Bellingham, WA 98225
    </address>
  </section>
</body>
</html>
```